Our business name is Quillbrook Pty Ltd and we already have a logo. We would like the same colours that appear in our logo on our marketing material. I have attached our logo for colour consistency. We need a brochure designed that promotes our aerial photography and aerial imaging services. We'd like to use the brochure for electronic marketing purposes in an effort to attract a new client base. We are a new start up business so funds are fairly scarce. We use sophisticated UAV (unmanned aerial vehicle) or RPA - remotely piloted aircraft technology) that captures beautiful video and still images.
Our services are suitable for many types of industries and applications. We have identified at least 10 market sectors ranging, infrastructure inspections such as: gas pipelines, chemical and petrol storage facilities, pipeline and power line inspections, Archeological and geological surveys, vegetation mapping, wildlife surveys, agriculture and horticulture surveys, high end real estate, sport and event marketing. Our plan is to create a series of brochures (1) for each industry to help us market our business.

Our first brochure will focus on environmental management and compliance. We will target other industries down the track. These industries would see our service as helping them meet their compliance and auditing requirements.
We have a brochure that we put together containing words and some (very boring) format. As this will be one of a series of brochures, we'd like to colour code the industries for easy identification. (perhaps a green tab) in the corner to distinguish between our brochures. We have attached our boring brochure as a starting point. If we like the design there will be more work to follow. We want to be able to standardise the format for the other industries we will target. We anticipate needing another 6-8 brochures over the course of the next 2 months.

I have received questions regarding brochure size.  Apologies, I should have indicated in my posting previously.  The brochure is A3 landscape size so it can be folded in half to make 4 A4 pages.  We need to keep printing costs down so the content needs to be  within 4 pages.  I'm about to make some minor changes to the content to try to reduce the amount of text cause I can see this may be a problem.  Look forward to receiving your design. Thanking you in advance for your great work!

Re: Brochure Quillbrook Environmental Compliance and Monitoring Services

I have reduced the amount of text contained in the original version of the brochure making it more succinct and less wordy.  Could you use the least amount of space because we want to be able to use this brochure as both electric marketing and print based.  I have also included additional photos which will give you more to work with.  Thank you for your work in advance!  Regards Marta 

PLEASE NOTE - TEXT HAS BEEN UPDATED (REDUCED TEXT IN BROCHURE). COULD YOU REFER TO VERSION 2 OF QUILLBROOK ENVIRONMENTAL COMPLIANCE AND MONITORING SERVICES BROCHURE UPDATED FRIDAY 17TH.

Thanks Marta 

Hi talented designers working on the Quillbrook Brochure for Environmental Compliance and Monitoring.  I have been asked to upload the EPS version of Quillbrook Logo.  I have just done so.

Regards
Marta 

Hi all, to assist you with the design concept. I feel I need to clarity a number of points.  We are a new technology driven business.  No one else is conducting environmental surveys using this type of sophisticated equipment. We are in the business of providing clients with visual data (aerial images). Could you include grab lines in the brochure that draws attention to this. We us state of the art technology to produce high quality images efficiently, safely and economically. 

Thank you
Marta

Reason: We need additional time to receive and review designs.

Reason: Need additional time to communicate with designers and to review changes. Thank you Marta

I have extended the project date a few days. I have been incredibly impressed by the quality of your work and thank you all for your efforts.  I am waiting on a few revisions by a number of designers and look forward to receiving these changes.  We are close to completion.  Thanking you all again. Marta 

We are targeting a wide range of industry sectors. Specifically, looking at targeting large engineering type consultancies, corporations, government agencies, auditing bodies. Typically, targeting the professional sector who use data to confirm, monitor and make better decisions.

We want the brochure design to be contemporary and modern which reflects what our business does. We use state of the art unmanned aerial technology to capture brilliant visual images and video. So we want our brochure to reflect that we're leaders in the field offering something different - cutting edge approach. I have additional photos that show vegetation mapping, wildlife surveys, agriculture and horticulture applications. Our services would benefit any business that uses visual data to help them make better, more informed decisions.

Business

Serif
Sans Serif

• We would like you to include photo of the UAV equipment/technology shots. This is new technology so we must also educate our clients on what our technology is capable of doing. We are offering a service that is very different so we want to be able to convey the true benefits of our services such as safety, efficiency, cost saving, reliability. We would like to convey these key themes. Credible data enables businesses to make better, faster decisions.
• We are essentially providing visual data in the form of high definition photos and videos. For this particular sector, data could be used for compliance or auditing purposes, planning, measuring, monitoring, evaluating, assessing, marketing. Could you please include these words in the brochure as they capture our service provision. Please note the red photo is infrared images.

```html
<!DOCTYPE html>
<html lang="en">
<head>
<meta charset="utf-8">
<title>Quillbrook – Aerial &amp; Spatial Imaging Brochure</title>
<link href="https://fonts.googleapis.com/css2?family=Jost:wght@400;500&family=Bitter:wght@400&family=Open+Sans:wght@400&display=swap" rel="stylesheet">
<style>
  :root {
    --brand-blue: #29a8e0;
    --brand-green: #6cbd45;
    --ink: #231f20;
    --text-grey: #8a8a8a;
    --paper: #ffffff;
    --paper-soft: #f3f5f6;
    --wash-blue: rgba(41, 168, 224, 0.10);
    --wash-green: rgba(108, 189, 69, 0.08);
    --sky-dark: #5e6462;
    --sky-light: #dfe2e1;
    --infrared-pink: #d9578f;
    --field-tan: #b9a79c;
    --lawn: #7dbb4a;
    --lawn-light: #93c85e;
    --tree-dark: #34502a;
  }
  * { margin: 0; padding: 0; box-sizing: border-box; }
  html, body { width: 1200px; height: 845px; overflow: hidden; background: var(--paper); }
  .brochure {
    position: relative; width: 1200px; height: 845px;
    background: var(--paper);
    font-family: "Open Sans", Arial, sans-serif;
  }

  .panel { position: absolute; }
  .panel--hero {
    left: 600px; top: 0; width: 600px; height: 308px;
    background:
      radial-gradient(ellipse 300px 170px at 360px 130px, var(--wash-green), transparent 70%),
      linear-gradient(180deg, var(--paper-soft), #fafbfb);
  }
  .panel--contact {
    left: 0; top: 311px; width: 601px; height: 423px;
    background:
      radial-gradient(ellipse 230px 260px at 470px 170px, var(--wash-blue), transparent 72%),
      radial-gradient(ellipse 380px 200px at 160px 40px, rgba(41, 168, 224, 0.05), transparent 75%),
      linear-gradient(180deg, #f5f7f8, var(--paper) 55%);
  }

  .photo { position: absolute; }
  .photo--infrared {
    left: 0; top: 0; width: 600px; height: 302px;
    background:
      radial-gradient(ellipse 420px 120px at 470px 40px, rgba(70, 75, 74, 0.55), transparent 75%),
      radial-gradient(ellipse 360px 60px at 500px 160px, rgba(150, 40, 80, 0.45), transparent 80%),
      linear-gradient(180deg,
        var(--sky-dark) 0%, #a7acaa 18%, var(--sky-light) 34%, #cfc9cc 44%,
        #8d5a73 49%, #c98aa6 53%, var(--infrared-pink) 64%,
        #c7889f 74%, var(--field-tan) 86%, #c15a8c 100%);
  }
  .photo--park {
    left: 601px; top: 318px; width: 599px; height: 409px;
    background:
      radial-gradient(ellipse 320px 170px at 420px 40px, rgba(52, 80, 42, 0.85), transparent 75%),
      radial-gradient(ellipse 160px 200px at 560px 300px, rgba(52, 80, 42, 0.6), transparent 75%),
      radial-gradient(ellipse 200px 90px at 90px 40px, rgba(52, 80, 42, 0.5), transparent 75%),
      linear-gradient(165deg, var(--lawn) 0%, var(--lawn-light) 45%, var(--lawn) 75%, #6aa53d 100%);
  }

  .rule { position: absolute; left: 0; width: 1200px; height: 3px; background: var(--brand-green); }
  .rule--mid { top: 308px; }
  .rule--low { top: 734px; }

  .wordmark { position: absolute; font-family: "Jost", Arial, sans-serif; font-weight: 400; color: var(--ink); line-height: 1; white-space: nowrap; }
  .wordmark--hero { left: 652px; top: 122px; font-size: 84px; letter-spacing: -2px; }
  .wordmark--contact { left: 34px; top: 490px; font-size: 42px; letter-spacing: -1px; }
  .tagline-logo { position: absolute; font-family: "Jost", Arial, sans-serif; color: var(--brand-blue); line-height: 1; white-space: nowrap; }
  .tagline-logo--hero { right: 80px; top: 214px; font-size: 23px; }
  .tagline-logo--contact { left: 122px; top: 533px; font-size: 11px; }

  .contact__icon { position: absolute; left: 36px; top: 575px; }
  .contact__title { position: absolute; left: 105px; top: 581px; font-size: 24px; font-weight: 400; color: var(--brand-blue); white-space: nowrap; }
  .contact__block { position: absolute; left: 127px; font-size: 12px; line-height: 16px; color: var(--text-grey); white-space: nowrap; }
  .contact__label { color: var(--brand-green); }
  .contact__block--address { top: 624px; }
  .contact__block--fax { top: 702px; }
  .spaced { letter-spacing: 2px; }

  .footer-band { position: absolute; left: 0; top: 745px; width: 1200px; height: 87px; background: var(--brand-blue); color: var(--paper); }
  .footer-band__phone { position: absolute; left: 106px; top: 12px; font-size: 12px; line-height: 17px; }
  .footer-band__slogan { position: absolute; right: 19px; top: 20px; font-family: "Bitter", Georgia, serif; font-size: 24px; white-space: nowrap; }
  .footer-band__web { position: absolute; right: 19px; top: 60px; font-size: 11px; letter-spacing: 3px; }
</style>
</head>
<body>
<main class="brochure">
  <div class="panel panel--hero"></div>
  <div class="panel panel--contact"></div>

  <div class="photo photo--infrared" role="img" aria-label="Infrared photograph of a grassy field under a cloudy sky, vegetation showing pink"></div>

  <div class="wordmark wordmark--hero">QUILLBROOK</div>
  <div class="tagline-logo tagline-logo--hero">AERIAL &amp; SPATIAL IMAGING</div>

  <div class="rule rule--mid"></div>

  <div class="photo photo--park" role="img" aria-label="Aerial view of parkland with trees, lawn and winding cycle paths"></div>

  <div class="wordmark wordmark--contact">QUILLBROOK</div>
  <div class="tagline-logo tagline-logo--contact">AERIAL &amp; SPATIAL IMAGING</div>

  <svg class="contact__icon" width="46" height="46" viewBox="0 0 46 46" aria-hidden="true">
    <circle cx="23" cy="23" r="20.5" fill="none" stroke="var(--brand-green)" stroke-width="2.5"/>
    <path d="M13 23h19M25 16l7 7-7 7" fill="none" stroke="var(--brand-green)" stroke-width="3" stroke-linecap="round" stroke-linejoin="round"/>
  </svg>
  <h2 class="contact__title">Contact Us</h2>

  <div class="contact__block contact__block--address">
    <div class="contact__label">Address:</div>
    <div>Quillbrook</div>
    <div>1234 Abcde Fghijkl, Mnopq 101</div>
    <div>Rstu Vwxyzab, 12345</div>
  </div>
  <div class="contact__block contact__block--fax">
    <div class="contact__label">Fax:</div>
    <div class="spaced">(789) 456-1230</div>
  </div>

  <div class="rule rule--low"></div>

  <footer class="footer-band">
    <div class="footer-band__phone">
      <div>Phone:</div>
      <div class="spaced">(123) 456-7890</div>
    </div>
    <div class="footer-band__slogan">Aerial Photography and Aerial Imaging Services</div>
    <div class="footer-band__web">www.quillbrook.com.au</div>
  </footer>
</main>
</body>
</html>
```